Redesign business cards

We have a new logo and I am not that happy with the layout of our existing card and looking for a change. Font is a bit small and the green can be hard to read. Logo may need a tidy up as the copy I have is not that hi-res too so require you to produce a hi-res version of the logo for us too. There will be three individual business cards to produce with just the names and phone numbers being different. Address will change too, but use what you see on the card for now.

Industry/Entity Type

Business

Requirements
Nice to have
• You could consider a redesign to the new logo, just not too radical. We like the blue and green hexagons as we feel that they are representative of oil industry that we are in.

```html
<!DOCTYPE html>
<html lang="en">
<head>
<meta charset="utf-8">
<title>NovaLube Oil Services – Business Card</title>
<link rel="stylesheet" href="https://fonts.googleapis.com/css2?family=Open+Sans:wght@400;600;700&display=swap">
<style>
  :root {
    --brand-blue: #0ea5e6;
    --brand-green: #8dc63f;
    --accent-orange: #f7941d;
    --text-grey: #555a5f;
    --muted-grey: #777c80;
    --card-white: #ffffff;
    --backdrop: #e9e6e1;
  }
  html, body {
    margin: 0;
    padding: 0;
    overflow: hidden;
  }
  body {
    width: 1200px;
    height: 829px;
    background: var(--backdrop);
    font-family: "Open Sans", sans-serif;
    position: relative;
  }
  .card {
    position: absolute;
    top: 266px;
    width: 520px;
    height: 297px;
    box-shadow: 0 6px 18px rgba(0,0,0,0.18);
    overflow: hidden;
  }
  .card-front { left: 60px; background: var(--card-white); }
  .card-back  { left: 620px; background: var(--brand-blue); }

  /* front: brand lockup */
  .brand {
    position: absolute;
    left: 34px;
    top: 44px;
    display: flex;
    align-items: center;
    gap: 12px;
    color: var(--brand-blue);
    font-weight: 700;
  }
  .brand-dot {
    width: 30px;
    height: 30px;
    border-radius: 50%;
    background: var(--brand-blue);
    flex: none;
  }
  .brand-name {
    font-size: 34px;
    line-height: 1;
    letter-spacing: -0.5px;
  }
  .brand-name small {
    display: block;
    font-size: 17px;
    letter-spacing: 0;
    margin-top: 4px;
  }

  /* front: person */
  .person {
    position: absolute;
    right: 30px;
    top: 38px;
    text-align: right;
  }
  .person-name,
  .person-credentials {
    color: var(--accent-orange);
    font-weight: 700;
    font-size: 15px;
    line-height: 1.3;
  }
  .person-role {
    color: var(--muted-grey);
    font-size: 11px;
    margin-top: 3px;
  }

  /* front: contact */
  .contact {
    position: absolute;
    left: 34px;
    top: 140px;
    color: var(--text-grey);
    font-size: 12.5px;
    line-height: 1.55;
  }
  .contact-line {
    display: flex;
    align-items: center;
    gap: 7px;
  }
  .contact-line svg { width: 12px; height: 12px; flex: none; }
  .address { margin-top: 10px; }

  /* front: footer band */
  .rule-green {
    position: absolute;
    left: 0; right: 0;
    top: 226px;
    height: 3px;
    background: var(--brand-green);
  }
  .band-blue {
    position: absolute;
    left: 0; right: 0;
    top: 232px;
    bottom: 0;
    background: var(--brand-blue);
    display: flex;
    align-items: center;
    padding-left: 34px;
  }
  .web {
    color: var(--card-white);
    font-size: 15px;
    letter-spacing: 4px;
  }

  /* back */
  .back-mark {
    position: absolute;
    left: 0; right: 0;
    top: 98px;
    text-align: center;
    color: var(--card-white);
    font-weight: 700;
    font-size: 34px;
  }
  .card-back .web {
    position: absolute;
    left: 0; right: 0;
    bottom: 52px;
    text-align: center;
  }
</style>
</head>
<body>

<section class="card card-front" aria-label="Business card front">
  <div class="brand">
    <span class="brand-dot"></span>
    <span class="brand-name">NovaLube<small>Oil Services</small></span>
  </div>

  <div class="person">
    <div class="person-name">Daniel Hartley</div>
    <div class="person-credentials">NZCE (Mech) P&amp;P</div>
    <div class="person-role">Director</div>
  </div>

  <div class="contact">
    <div class="contact-line">
      <svg viewBox="0 0 12 12" aria-hidden="true">
        <circle cx="6" cy="6" r="5.3" fill="none" stroke="var(--accent-orange)" stroke-width="1.2"/>
        <path d="M4 3.2 L5.2 3.2 L5.6 4.6 L4.9 5.2 Q5.6 6.6 6.9 7.2 L7.5 6.5 L8.8 6.9 L8.8 8.1 Q5 8.6 3.9 4.1 Z" fill="var(--accent-orange)"/>
      </svg>
      <span>+61 4 555 01234</span>
    </div>
    <div class="contact-line">
      <svg viewBox="0 0 12 12" aria-hidden="true">
        <rect x="0.8" y="2.5" width="10.4" height="7" rx="1" fill="var(--accent-orange)"/>
        <path d="M1.2 3 L6 6.6 L10.8 3" fill="none" stroke="#fff" stroke-width="1"/>
      </svg>
      <span>daniel@novalube.co.nz</span>
    </div>
    <div class="address">
      NovaLube Oil Services 210 Harbour Road<br>
      PO Box 4410 | Eastwood Queensland 4000
    </div>
  </div>

  <div class="rule-green"></div>
  <div class="band-blue"><span class="web">www.novalube.com.au</span></div>
</section>

<section class="card card-back" aria-label="Business card back">
  <div class="back-mark">NovaLube</div>
  <span class="web">www.novalube.com.au</span>
</section>

</body>
</html>
```